Tech business card design

We need an amazing business card design for our new business 'Pexla' a marketing tech startup based in Sydney, Australia. We provide an online marketplace for businesses to search and buy advertising media, connect with service providers and learn more about marketing. We wish to communicate 'cool tech', reliability and professionalism and design based around our logo.

Target Market(s)

Business Owners

Contact Information for Business Card

Name
Position
Email Address
Website
Phone Number

Font styles to use
Other font styles liked:
• Avenir & Avenir Next

Colors

Designer to choose colors to be used in the design.

```html
<!DOCTYPE html>
<html lang="en">
<head>
<meta charset="utf-8">
<title>Pexla Business Card</title>
<link rel="stylesheet" href="https://fonts.googleapis.com/css2?family=Nunito+Sans:wght@400;700;900&display=swap">
<style>
  :root {
    --stage: #1c1c1e;
    --navy: #141a48;
    --navy-back: #1a2150;
    --grey: #707172;
    --white: #ffffff;
    --ink: #222222;
    --faint-mark: #565d8c;
  }
  * { margin: 0; padding: 0; box-sizing: border-box; }
  html, body {
    width: 1200px; height: 803px; overflow: hidden;
    background: var(--stage);
    font-family: "Nunito Sans", Arial, sans-serif;
  }
  .stage {
    position: relative; width: 1200px; height: 803px;
    display: flex; align-items: center; justify-content: center; gap: 50px;
  }
  .card {
    position: relative; width: 540px; height: 310px;
    border-radius: 4px; overflow: hidden;
    box-shadow: 0 12px 30px rgba(0,0,0,.5);
  }
  .card--front { background: var(--white); }
  .card--back { background: var(--navy-back); display: flex; align-items: center; justify-content: center; }
  .front-shapes { position: absolute; inset: 0; }
  .brand-name {
    position: absolute; left: 30px; top: 62px;
    font-weight: 900; font-size: 84px; line-height: 1;
    letter-spacing: -2px; color: var(--navy);
  }
  .person {
    position: absolute; right: 30px; top: 26px; text-align: right; color: var(--navy);
  }
  .person__name { font-weight: 900; font-size: 17px; letter-spacing: .5px; }
  .person__role { font-weight: 700; font-size: 12px; color: #333a5c; }
  .address {
    position: absolute; left: 36px; top: 166px;
    font-size: 12.5px; line-height: 1.25; color: var(--ink);
  }
  .contacts {
    position: absolute; left: 36px; top: 228px; list-style: none;
    color: var(--white); font-size: 13px;
  }
  .contacts li { display: flex; align-items: center; gap: 9px; height: 24px; }
  .contacts svg { width: 12px; height: 12px; fill: var(--white); }
  .back-name {
    font-weight: 900; font-size: 150px; letter-spacing: -4px;
    color: var(--faint-mark); line-height: 1;
  }
</style>
</head>
<body>
<main class="stage">
  <section class="card card--front" aria-label="Business card front">
    <svg class="front-shapes" viewBox="0 0 540 310" aria-hidden="true">
      <path fill="var(--navy)" d="M0 212 H235 C268 212 276 150 318 150 H398 Q420 150 428 170 L436 196 H540 V310 H0 Z"/>
      <path fill="var(--grey)" d="M468 128 H540 V186 H446 V150 Q446 128 468 128 Z"/>
    </svg>
    <div class="brand-name">Pexla</div>
    <div class="person">
      <div class="person__name">LIAM CARTER</div>
      <div class="person__role">Position</div>
    </div>
    <p class="address">Street Name, City Name<br>Zipcode 012345</p>
    <ul class="contacts">
      <li><svg viewBox="0 0 12 12"><path d="M2.5 1 L4.5 1 L5.3 3.5 L4 4.5 Q5 6.8 7.5 8 L8.5 6.7 L11 7.5 V9.5 Q11 11 9.5 11 Q1 10 1 2.5 Q1 1 2.5 1Z"/></svg>012-345-6789</li>
      <li><svg viewBox="0 0 12 12"><path d="M0 2 H12 V10 H0 Z M1 3 L6 7 L11 3" stroke="var(--navy)" stroke-width="1"/></svg>info@pexla.com</li>
      <li><svg viewBox="0 0 12 12"><circle cx="6" cy="6" r="5.5"/><path d="M0.5 6 H11.5 M6 0.5 V11.5 M6 0.5 Q2.5 6 6 11.5 M6 0.5 Q9.5 6 6 11.5" stroke="var(--navy)" stroke-width=".8" fill="none"/></svg>www.pexla.com</li>
    </ul>
  </section>

  <section class="card card--back" aria-label="Business card back">
    <div class="back-name">Pexla</div>
  </section>
</main>
</body>
</html>
```